Business Card Design Project

We are looking to redesign the logo, business card and stationary of one of our group companies - SOLARO SUPPLY HOUSE LLC.

The company specialises in industrial PVC and CPVC Piping systems. It is situated in the Middle East and the focus is purely in this region.

The logo work is already completed. The file is uploaded for the reference.

We are looking for a clean minimalistic design for the business card.

regards
Rohit
Updates

Hello Everyone!

Thanks for submitting your designs. 

Yet to find the right design. Probably the below links will give you guys some more idea on what we would like.

Minimalist design with some creativity.

Rohit

http://exampledesignfolio.com/inspiration/15-beautifully-minimal-business-cards

http://www.samplelayoutbase.com/2011/11/14/30-minimalist-business-card-design/

http://www.primepixelcraft.com/inspiration/minimal-business-cards/

Target Market(s)

Industrial users

Industry/Entity Type

Industrial

Requirements
Must have
• - Minimalistic design

- Back side of the card should include the manufacturer PIPEMARQ NORTHERN's decal. The file is upload for the reference

- Further information
Company Name:
SOLARO SUPPLY HOUSE LLC
Address:
PO Box 8152, Sharjah Industrial Area 4, Qarwan Road
Sharjah, United Arab Emirates
Telephone:
+971-6-5000-118
Fax:
+977-6-5000-119
Email:
mail@sshlexample.com

- FYI, Solaro Supply House LLC is the authorised distributor for PIPEMARQ NORTHERN in the UAE. For further information on pipemarq please visit the website www.pipemarq-example.ca

```html
<!DOCTYPE html>
<html lang="en">
<head>
<meta charset="utf-8">
<title>Solaro Supply House LLC – Business Card</title>
<link rel="stylesheet" href="https://fonts.googleapis.com/css2?family=Arimo:wght@700&display=swap">
<style>
  :root {
    --card-bg: #f4f4f4;
    --fitting-light: #ececec;
    --fitting-mid: #d6d6d6;
    --brand-blue: #3a80c9;
    --brand-dark: #1f55a6;
    --address-grey: #6b6b6b;
    --mark-frame: #2e2e2e;
  }
  * { margin: 0; padding: 0; box-sizing: border-box; }
  html, body {
    width: 1200px;
    height: 686px;
    overflow: hidden;
    background: #ffffff;
  }
  .card {
    position: relative;
    width: 1200px;
    height: 686px;
    overflow: hidden;
    background: var(--card-bg);
    font-family: "Arimo", Arial, sans-serif;
    font-weight: 700;
  }
  .fittings-backdrop {
    position: absolute;
    inset: 0;
    background:
      radial-gradient(ellipse 300px 260px at 330px 520px, var(--fitting-mid), transparent 70%),
      radial-gradient(ellipse 330px 300px at 850px 420px, var(--fitting-mid), transparent 70%),
      radial-gradient(ellipse 260px 220px at 620px 170px, var(--fitting-light), transparent 70%),
      linear-gradient(135deg, #f7f7f7, #e9e9e9 55%, #f3f3f3);
  }
  .brand-mark {
    position: absolute;
    left: 23px;
    top: 26px;
    width: 320px;
    display: flex;
    flex-direction: column;
    align-items: center;
    gap: 10px;
  }
  .brand-mark__square {
    width: 246px;
    height: 246px;
    border-radius: 52px;
    background: var(--mark-frame);
  }
  .brand-mark__name {
    color: var(--brand-blue);
    font-size: 42px;
    line-height: 50px;
    letter-spacing: 1px;
  }
  .company-name {
    position: absolute;
    left: 380px;
    top: 20px;
    width: 710px;
    text-align: center;
    color: var(--brand-blue);
    font-size: 70px;
    line-height: 91px;
    text-shadow: 2px 3px 4px rgba(0,0,0,0.18);
  }
  .contact {
    position: absolute;
    right: 17px;
    top: 219px;
    text-align: right;
    font-style: normal;
    font-size: 41px;
    line-height: 57px;
    color: var(--address-grey);
  }
  .contact__phone { color: var(--brand-dark); }
  .email {
    position: absolute;
    left: 295px;
    top: 626px;
    font-size: 41px;
    line-height: 50px;
    color: var(--brand-blue);
  }
</style>
</head>
<body>
  <div class="card">
    <div class="fittings-backdrop" role="img" aria-label="Faint photograph of PVC pipe fittings across the background"></div>

    <div class="brand-mark">
      <div class="brand-mark__square"></div>
      <span class="brand-mark__name">SOLARO</span>
    </div>

    <h1 class="company-name">SOLARO SUPPLY<br>HOUSE LLC</h1>

    <address class="contact">
      <div>PO Box 8152</div>
      <div>Sharjah Industrial Area 4</div>
      <div>Qarwan Road</div>
      <div>Sharjah</div>
      <div>United Arab Emirates</div>
      <div class="contact__phone">Tel: +971-6-5000-118</div>
      <div class="contact__phone">Fax: +977-6-5000-119</div>
    </address>

    <div class="email">Email: mail@sshlexample.com</div>
  </div>
</body>
</html>
```